New Website for World Wide Charity (KOLVAN)

We need a dynamic web design for our brand new charity organisation that will be working worldwide. We will be funded by donations so need to attract people to donate.

What We Do
We work to optimise the wellbeing of the planet, the animals and all that live within. Our slogan is Achieving Vibrational Equilibrium.

We have included a Powerpoint document which may help you understand what we need, it is just an idea for structure and style, it is not set in stone so feel free to be as creative as you like!
Updates

Designs look the same

Target Market(s)

Adults 18+ with an interest in animal, environmental. Businesses that may like to support our natural world or already support our natural world.

Number of Pages Required

3 page

Colors

Designer to choose colors to be used in the design.

Requirements
Must have
• We need the website to be easy to use and understand.

Web pages will be Home, What We Do, Who We Are, Success Stories, What You Can Do (Blog section), Seek Help, Donate, Join.
Nice to have
• Natural feel, easy to navigate, Ideally the website will look natural and organic.

Natural colours, blues, greens, sand, gold, brown, grey, silver, Orange and yellow for impact.
Should not have
• Should not have a dark coloured theme.

```html
<!DOCTYPE html>
<html lang="en">
<head>
<meta charset="utf-8">
<title>Kolvan — Achieving Vibrational Equilibrium</title>
<link rel="stylesheet" href="https://fonts.googleapis.com/css2?family=Fira+Sans+Condensed:ital,wght@0,700;1,700&family=Roboto:wght@400;500;700&display=swap">
<style>
:root{
  --green:#23753a;
  --green-dark:#1b5e2e;
  --navy:#24468c;
  --blue-text:#2b4c94;
  --body:#555a60;
  --page:#f2f4f7;
  --white:#ffffff;
  --line:#d8dce2;
}
*{box-sizing:border-box;margin:0;padding:0}
html,body{width:1200px;height:3367px;overflow:hidden}
body{position:relative;background:linear-gradient(180deg,#f4f5f8 0%,#eef1f4 40%,#f3f4f6 75%,#f1f3f5 100%);font-family:"Roboto",sans-serif;color:var(--body)}
.abs{position:absolute}
.btn{position:absolute;display:flex;align-items:center;justify-content:center;gap:8px;background:var(--green);color:var(--white);font-family:"Roboto",sans-serif;font-weight:700;font-size:15px;border-radius:22px;text-transform:uppercase;letter-spacing:.2px}

/* header */
.site-header{position:absolute;left:0;top:0;width:1200px;height:97px;background:var(--white)}
.brand{position:absolute;left:98px;top:8px;width:138px;height:128px;border-radius:50%;background:var(--white);border:4px solid #c9d2e6;display:flex;align-items:center;justify-content:center;z-index:3;box-shadow:0 2px 6px rgba(0,0,0,.12)}
.brand span{font-family:"Roboto",sans-serif;font-weight:500;font-size:20px;color:var(--navy);letter-spacing:1px}
.nav{position:absolute;top:61px;left:347px;display:flex;gap:0;font-size:15.5px;color:var(--navy)}
.nav a{text-decoration:none;color:inherit;text-transform:uppercase;margin-right:62px}
.nav a:last-child{margin-right:0}
.nav a.active{color:var(--green);font-weight:700}
.btn-donate{left:826px;top:13px;width:132px;height:36px;background:var(--navy);font-size:14px}
.btn-join{left:967px;top:13px;width:132px;height:36px;font-size:14px}

/* hero */
.hero{position:absolute;left:0;top:97px;width:1200px;height:596px;background:linear-gradient(100deg,#8a5a22 0%,#d99a2b 30%,#f2b53a 45%,#e08a1c 65%,#9c5a1c 85%,#6d3c14 100%)}
.hero::after{content:"";position:absolute;left:0;right:0;bottom:0;height:230px;background:linear-gradient(180deg,rgba(120,80,50,0) 0%,rgba(110,80,60,.55) 100%)}
.hero-title{position:absolute;left:590px;top:184px;font-family:"Fira Sans Condensed",sans-serif;font-weight:700;font-size:62px;line-height:62px;color:var(--white);z-index:2;text-transform:uppercase}
.hero .btn{left:590px;top:331px;width:200px;height:40px;z-index:2}
.hero-arrow{position:absolute;top:265px;z-index:2}
.dots{position:absolute;left:565px;top:516px;display:flex;gap:8px;z-index:2}
.dots i{width:12px;height:12px;border-radius:50%;border:1.5px solid var(--white)}
.dots i.on{background:var(--white)}
.hero-edge{position:absolute;left:0;top:680px;width:1200px;height:22px}

/* focus circles */
.focus{position:absolute;top:763px;width:290px;text-align:center}
.focus-ring{width:288px;height:288px;border-radius:50%;border:4px solid #e4e7ec;position:relative;overflow:hidden;box-shadow:0 3px 10px rgba(0,0,0,.1)}
.focus-ring .img{position:absolute;inset:14px;border-radius:50%}
.focus-ring .band{position:absolute;left:0;right:0;top:124px;height:40px;background:rgba(243,245,248,.96);font-size:25px;color:var(--navy);line-height:40px;font-weight:500}
.focus .btn{position:relative;margin:14px auto 0;width:176px;height:40px}

.slogan{position:absolute;left:0;width:1200px;top:1200px;text-align:center;font-family:"Fira Sans Condensed",sans-serif;font-style:italic;font-weight:700;font-size:42px;color:var(--navy)}

/* feature rows */
.feature-img{position:absolute}
.feature h2{position:absolute;font-family:"Fira Sans Condensed",sans-serif;font-weight:700;font-size:46px;color:var(--navy);text-transform:uppercase}
.feature p{position:absolute;width:460px;font-size:15px;line-height:25.6px;color:var(--body)}
.feature .btn{width:144px;height:41px}

/* footer */
.footer h3{position:absolute;font-size:21px;font-weight:500;color:var(--navy)}
.footer ul{position:absolute;list-style:none;font-size:13px;line-height:25px;color:#333}
.vline{position:absolute;width:1px;background:var(--line)}
.foot-logo{position:absolute;left:494px;top:2822px;width:160px;height:152px;border-radius:50%;border:4px solid #c9d2e6;background:var(--white);display:flex;align-items:center;justify-content:center}
.foot-logo span{font-size:22px;font-weight:500;color:var(--navy);letter-spacing:1px}
.charity{position:absolute;left:514px;top:3004px;display:flex;align-items:center;gap:6px}
.charity small{display:block;font-size:10px;color:#555}
.charity b{display:block;font-size:15px;color:#222}
.news-input{position:absolute;left:776px;top:2911px;width:263px;height:37px;border:1px solid var(--line);background:var(--white);font-size:11px;color:#555;padding:11px 16px}
.bottom-scene{position:absolute;left:0;top:3030px;width:1200px;height:337px;background:linear-gradient(180deg,rgba(242,244,247,1) 0%,rgba(230,214,160,.6) 22%,#c9b86a 40%,#8fae45 65%,#5f8a2a 100%)}
.legal{position:absolute;top:3067px;font-size:13.5px;color:#333}
</style>
</head>
<body>

<header class="site-header">
  <div class="brand"><span>KOLVAN</span></div>
  <nav class="nav">
    <a class="active">Home</a><a>What We Do</a><a>Who We Are</a><a>Success Stories</a><a>What You Can Do</a>
  </nav>
  <a class="btn btn-donate">
    <svg width="15" height="14" viewBox="0 0 24 22" fill="none" stroke="#fff" stroke-width="2.5"><path d="M12 20S2 13.5 2 7.5A5 5 0 0 1 12 5a5 5 0 0 1 10 2.5C22 13.5 12 20 12 20z"/></svg>DONATE</a>
  <a class="btn btn-join">
    <svg width="12" height="13" viewBox="0 0 12 13" fill="#fff"><circle cx="6" cy="3.5" r="3.2"/><path d="M0 13c0-4 2.6-6 6-6s6 2 6 6z"/></svg>JOIN</a>
</header>

<section class="hero" role="img" aria-label="Stag standing in frosty grass at a golden sunrise forest">
  <div class="hero-title">Help Raise<br>World Vibration</div>
  <a class="btn">Make a Difference</a>
  <svg class="hero-arrow" style="left:62px" width="18" height="34" viewBox="0 0 18 34" fill="none" stroke="#fff" stroke-width="2"><path d="M16 2 2 17l14 15"/></svg>
  <svg class="hero-arrow" style="left:1128px" width="18" height="34" viewBox="0 0 18 34" fill="none" stroke="#fff" stroke-width="2"><path d="M2 2l14 15L2 32"/></svg>
  <div class="dots"><i class="on"></i><i></i><i></i><i></i></div>
</section>
<svg class="hero-edge" viewBox="0 0 1200 22" preserveAspectRatio="none"><path d="M0 0h1200v10l-40 6-60-4-80 7-90-5-70 6-100-5-80 6-90-4-70 5-110-6-90 6-80-4-100 5-70-5-90 6-80-4L0 14z" fill="#1e1a16"/></svg>

<div class="focus" style="left:111px">
  <div class="focus-ring"><div class="img" role="img" aria-label="Pine forest" style="background:linear-gradient(180deg,#7aa58a,#2f6b3a)"></div><div class="band">ENVIRONMENT</div></div>
  <a class="btn">Find Out More <span>»</span></a>
</div>
<div class="focus" style="left:458px">
  <div class="focus-ring"><div class="img" role="img" aria-label="Group of wild animals" style="background:linear-gradient(180deg,#dfe9f3,#b3a280 60%,#6b5a40)"></div><div class="band">ANIMAL</div></div>
  <a class="btn">Find Out More <span>»</span></a>
</div>
<div class="focus" style="left:805px">
  <div class="focus-ring"><div class="img" role="img" aria-label="People with arms raised in a golden field" style="background:linear-gradient(180deg,#f3c27a,#c98a3a 55%,#8a5a24)"></div><div class="band">HUMAN</div></div>
  <a class="btn">Find Out More <span>»</span></a>
</div>

<h1 class="slogan">ACHIEVING VIBRATIONAL EQUILIBRIUM</h1>

<section class="feature">
  <div class="feature-img" role="img" aria-label="Mountain lake under blue sky" style="left:600px;top:1361px;width:507px;height:460px;background:linear-gradient(180deg,#3f86d6 0%,#b9d2ea 30%,#4f7d4a 45%,#245aa0 60%,#0f3a78 100%)"></div>
  <h2 style="left:99px;top:1414px">Environment</h2>
  <p style="left:100px;top:1483px">Lorem ipsum dolor sit amet, consectetur adipiscing elit, sdo eiusmod tempor incididunt ut labore et dolore magna aliqua. Quu suspendisse ultrices gravida. Risus commodo viverra maecenan lacus vel facilisis. Lorem ipsum dolor sit amet, consectetur adiping elit, sed do eiusmod tempor incididunt ut labore et dolore magna am suspendisse ultrices gravida. Risus commodo viverra maecenas amsan lacus vel facilisis. Lorem ipsum dolor sit amet, consectetur adipiscing elit, sdo eiusmod tempor incididunt ut labore et dolore magna aliqua.</p>
  <a class="btn" style="left:100px;top:1715px">Read More</a>
</section>

<section class="feature">
  <div class="feature-img" role="img" aria-label="Elephant beside a safari vehicle" style="left:100px;top:1821px;width:501px;height:460px;background:linear-gradient(180deg,#5a9ad8 0%,#9cc2e4 20%,#3d6b2e 40%,#7c8a60 75%,#5a4a34 100%)"></div>
  <h2 style="left:638px;top:1874px">Animal</h2>
  <p style="left:640px;top:1943px">Lorem ipsum dolor sit amet, consectetur adipiscing elit, sdo eiusmod tempor incididunt ut labore et dolore magna aliqua. Quu suspendisse ultrices gravida. Risus commodo viverra maecenan lacus vel facilisis. Lorem ipsum dolor sit amet, consectetur adiping elit, sed do eiusmod tempor incididunt ut labore et dolore magna am suspendisse ultrices gravida. Risus commodo viverra maecenas amsan lacus vel facilisis. Lorem ipsum dolor sit amet, consectetur adipiscing elit, sdo eiusmod tempor incididunt ut labore et dolore magna aliqua.</p>
  <a class="btn" style="left:640px;top:2175px">Read More</a>
</section>

<section class="feature">
  <div class="feature-img" role="img" aria-label="Hiker in red jacket on a summit above the clouds" style="left:600px;top:2280px;width:501px;height:460px;background:linear-gradient(180deg,#1f4f9a 0%,#5d86c0 30%,#c9d4e0 55%,#8a94a0 75%,#4a4a4a 100%)"></div>
  <h2 style="left:99px;top:2333px">Human</h2>
  <p style="left:100px;top:2402px">Lorem ipsum dolor sit amet, consectetur adipiscing elit, sdo eiusmod tempor incididunt ut labore et dolore magna aliqua. Quu suspendisse ultrices gravida. Risus commodo viverra maecenan lacus vel facilisis. Lorem ipsum dolor sit amet, consectetur adiping elit, sed do eiusmod tempor incididunt ut labore et dolore magna am suspendisse ultrices gravida. Risus commodo viverra maecenas amsan lacus vel facilisis. Lorem ipsum dolor sit amet, consectetur adipiscing elit, sdo eiusmod tempor incididunt ut labore et dolore magna aliqua.</p>
  <a class="btn" style="left:100px;top:2634px">Read More</a>
</section>

<div class="bottom-scene" role="img" aria-label="Sunlit rocky meadow landscape"></div>

<footer class="footer">
  <h3 style="left:98px;top:2832px">Get Involved</h3>
  <ul style="left:99px;top:2870px"><li>JOIN US</li><li>FUNDRAISE</li><li>DONATE</li><li>SHOP</li></ul>
  <h3 style="left:292px;top:2832px">Get Help</h3>
  <ul style="left:293px;top:2870px"><li>CONTACT US</li><li>MEDIA</li></ul>
  <div class="vline" style="left:435px;top:2818px;height:182px"></div>
  <div class="foot-logo"><span>KOLVAN</span></div>
  <div class="abs" style="left:488px;top:2994px;width:192px;height:1px;background:var(--line)"></div>
  <div class="charity">
    <svg width="16" height="26" viewBox="0 0 16 26" fill="none" stroke="#2f8a3e" stroke-width="2"><rect x="1" y="1" width="14" height="24" rx="2"/><path d="M6 21h4"/></svg>
    <div><small>Charity Number</small><b>555-010-0199</b></div>
  </div>
  <div class="vline" style="left:716px;top:2818px;height:182px"></div>
  <h3 style="left:776px;top:2824px">Newsletter</h3>
  <p class="abs" style="left:776px;top:2866px;width:270px;font-size:13px;line-height:18px;color:#333">Subscribe to my newsletter to get updates in your inbox!</p>
  <div class="news-input">Enter Your Email Address</div>
  <a class="btn" style="left:776px;top:2961px;width:144px;height:36px;font-size:12px">Subscribe Now</a>
  <div class="abs" style="left:98px;top:3050px;width:1002px;height:1px;background:#c9cdd3"></div>
  <div class="legal" style="left:156px">© 2021 Kolvan. All Rights Reserved.</div>
  <div class="legal" style="left:799px">Terms and Conditions&nbsp;&nbsp; Cookies&nbsp;&nbsp; Privacy Policy</div>
</footer>

</body>
</html>
```